KAJU Freightways #ALLKAJU Business Cards & Letterhead

I am looking to business cards designed for our organization. We are currently undergoing a small re-branding that is taking place. Our organization is called KAJU Freightways and we are headquartered in Phoenix, AZ. We primarily provide transportation and logistics services to the Marlow Parcel Bureau who is our largest customer. I would like to see a design that incorporates name, title, contact info, website, and address (this will be different depending on the employee). I would also like to see some color on the business card using our logo colors or a variation. I would like our logo on the back of the business card with the website displayed. The final design should communicate that we are a next generation transportation operate that focuses on being driver-first, customer-centric, innovative, and sustainable.We would also like our #ALLKAJU catch phrase incorporated as well.

Target Market(s)

Transportation & Logistics

Industry/Entity Type

Trucking Company

Contact Information for Business Card

-First and Last Name
-Position Title
-Contact Phone
-Contact Email
-Physical Address

Font styles to use
Serif

Colors

Designer to choose colors to be used in the design.

Requirements
Must have
• -KAJU logo prominently displayed
• -#ALLKAJU catch phrase used
• -Some amount of color, design gradient, etc.
• -Logo on the back with website listed (https://www.kajufreightco.example)

```html
<!DOCTYPE html>
<html lang="en">
<head>
<meta charset="utf-8">
<title>KAJU Freightways Business Card</title>
<link href="https://fonts.googleapis.com/css2?family=Roboto:wght@300;400;500&display=swap" rel="stylesheet">
<style>
  :root {
    --teal: #053b49;
    --teal-light: #0b4856;
    --green: #7dc242;
    --white: #ffffff;
    --paper: #c8c8c8;
  }
  * { margin: 0; padding: 0; box-sizing: border-box; }
  html, body {
    width: 1125px; height: 1200px; overflow: hidden;
    background: var(--paper);
    font-family: "Roboto", Arial, sans-serif;
  }
  .card {
    position: absolute; left: 150px; width: 826px; height: 472px;
    border-radius: 24px; overflow: hidden;
  }
  .card--front { top: 98px; background: var(--teal); }
  .card--back { top: 631px; background: var(--teal); }
  .card__shape { position: absolute; inset: 0; }

  .brand-name {
    position: absolute; transform: translate(-50%, -50%);
    font-weight: 500; letter-spacing: 1px; line-height: 1; white-space: nowrap;
  }
  .card--front .brand-name { left: 180px; top: 234px; color: var(--teal); font-size: 64px; }
  .card--back .brand-name { left: 413px; top: 222px; color: var(--white); font-size: 72px; }

  .back-info {
    position: absolute; left: 0; right: 0; top: 292px; text-align: center;
    color: var(--white); font-weight: 300;
  }
  .back-info__tag { color: var(--green); font-size: 22px; font-weight: 400; letter-spacing: 1px; }
  .back-info__web { font-size: 18px; margin-top: 8px; }

  .contact {
    position: absolute; left: 467px; top: 130px; color: var(--white);
    font-weight: 300;
  }
  .contact__name { color: var(--green); font-size: 28px; font-weight: 400; line-height: 1.1; }
  .contact__title { font-size: 20px; line-height: 1.3; }
  .contact__address { font-size: 20.5px; line-height: 1.27; margin-top: 10px; }
  .contact__list { list-style: none; margin-top: 12px; font-size: 20.5px; }
  .contact__item { display: flex; align-items: center; height: 26px; }
  .contact__icon { width: 16px; height: 16px; margin-right: 13px; fill: var(--green); }
  .contact__accent { color: var(--green); }

  .world-map {
    position: absolute; left: 10px; top: 6px; width: 806px; height: 444px;
    background: radial-gradient(ellipse at center, var(--teal-light) 0%, var(--teal) 75%);
    opacity: 0.9;
  }
</style>
</head>
<body>
  <section class="card card--front">
    <svg class="card__shape" viewBox="0 0 826 472" aria-hidden="true">
      <path d="M0 0 L428 0 C445 190 390 370 232 472 L0 472 Z" fill="#7dc242"/>
      <path d="M0 0 L426 0 C433 160 385 355 196 472 L0 472 Z" fill="#ffffff"/>
    </svg>
    <span class="brand-name">KAJU</span>
    <div class="contact">
      <p class="contact__name">Dana Whitfield</p>
      <p class="contact__title">Manager</p>
      <p class="contact__address">4710 North Canyon Ridge Road<br>Glendale, AZ 85310</p>
      <ul class="contact__list">
        <li class="contact__item">
          <svg class="contact__icon" viewBox="0 0 16 16"><path d="M3.5 1 L6 4 L4.5 6 C5.5 8 8 10.5 10 11.5 L12 10 L15 12.5 L13 15 C7 14.5 1.5 9 1 3 Z"/></svg>
          602-555-0148
        </li>
        <li class="contact__item">
          <svg class="contact__icon" viewBox="0 0 16 16"><path d="M1 3 H15 V13 H1 Z M2 4 L8 9 L14 4 Z" fill-rule="evenodd"/></svg>
          info@kajufreightco.example
        </li>
        <li class="contact__item">
          <svg class="contact__icon" viewBox="0 0 16 16"><circle cx="8" cy="8" r="7"/></svg>
          www.<span class="contact__accent">kajufreightco</span>.example
        </li>
      </ul>
    </div>
  </section>

  <section class="card card--back">
    <div class="world-map" role="img" aria-label="Faint dotted world map in dark teal tones"></div>
    <span class="brand-name">KAJU</span>
    <div class="back-info">
      <p class="back-info__tag">#ALLKAJU</p>
      <p class="back-info__web">www.kajufreightco.example</p>
    </div>
  </section>
</body>
</html>
```